Velmor Spire Nine Flash website

we need a website to cater to 2 aspect of the business. We have Velmor spire residence and velmor spire office. For the office, we will get their inquire and arrange a face to face meetup to show them the office area for rent. For the residence side, it will need to be like staylane or roomvio.com. we want to allow them to book online for the date they need. We have a total of 10 different room configurations starting at $70 per night and up depending on the size of the room. example of the design is https://brisquelodge.com/

Target Market(s)

the website should have detail information on the layout, designs, and luxury of the building.

Industry/Entity Type

office and service appartment rental/lease

Coding

Coded - Design and coding required

Number of Pages Required

5+ page

Requirements
Must have
• a luxury perspective
Nice to have
• example https://brisquelodge.com/

```html
<!DOCTYPE html>
<html lang="en">
<head>
<meta charset="utf-8">
<title>Velmor Spire Nine – Website Screens</title>
<link href="https://fonts.googleapis.com/css2?family=Cinzel:wght@400;500;600&family=Lato:wght@400;700&family=Open+Sans:wght@400;600;700&display=swap" rel="stylesheet">
<style>
:root{
  --gold:#d4982b;
  --gold-soft:#e0ad4e;
  --black:#000;
  --ink:#1d1d1d;
  --muted:#555;
  --line:#e3e3e3;
  --white:#fff;
}
*{box-sizing:border-box;margin:0;padding:0}
html,body{width:816px;height:1200px;overflow:hidden;background:var(--white)}
body{position:relative;font-family:'Lato',sans-serif;color:var(--ink)}
h1,h2,h3{font-weight:400}
.screen{position:absolute;width:688px;transform-origin:0 0;transform:scale(0.516);overflow:hidden;box-shadow:0 0 8px rgba(0,0,0,.18)}
.screen--landing{left:32px;top:28px;height:398px;background:#050505}
.screen--home{left:424px;top:28px;height:2170px;background:var(--white)}
.abs{position:absolute}
.serif{font-family:'Cinzel',serif}
.brand{font-family:'Cinzel',serif;color:var(--gold);font-size:10px;display:flex;align-items:center;gap:4px;white-space:nowrap}
.brand__mark{width:7px;height:7px;background:var(--gold)}
.site-header{position:absolute;left:0;top:0;width:688px;height:54px;background:var(--black)}
.site-header .brand{position:absolute;left:57px;top:38px}
.nav{position:absolute;left:301px;top:22px;display:flex;gap:20px;font-family:'Cinzel',serif;font-size:9px;color:var(--gold)}
.pill{position:absolute;background:var(--gold);color:var(--white);border-radius:14px;font-family:'Cinzel',serif;font-size:9px;display:flex;align-items:center;justify-content:center;font-weight:400;white-space:nowrap}
.pill--outline{background:transparent;border:2px solid var(--gold);color:var(--gold)}
.landing-bg{position:absolute;left:0;top:59px;width:688px;height:339px;background:radial-gradient(ellipse at 50% 40%,#2a2a2a 0%,#111 45%,#020202 100%)}
.landing-rule{position:absolute;left:0;top:58px;width:688px;height:1px;background:#6b5220}
.landing-title{position:absolute;left:0;width:688px;top:158px;text-align:center;font-family:'Cinzel',serif;font-size:31px;color:var(--white)}
.landing-copy{position:absolute;left:0;width:688px;top:206px;text-align:center;font-size:8.5px;line-height:20px;color:#ddd}
.hero{position:absolute;left:0;top:54px;width:688px;height:346px;background:linear-gradient(100deg,#5c9fd9 0%,#9cc8ee 35%,#e9eef2 60%,#c9d3dc 100%)}
.hero-title{position:absolute;left:57px;top:134px;font-family:'Cinzel',serif;font-size:26px;line-height:34px;color:#111}
.hero-copy{position:absolute;left:57px;top:240px;font-size:8.5px;line-height:18px;color:#222}
.finder{position:absolute;left:0;top:400px;width:688px;height:94px}
.finder__label{position:absolute;left:140px;top:17px;font-family:'Cinzel',serif;color:var(--white);font-size:15px}
.finder__fields{position:absolute;left:140px;top:47px;width:444px;height:29px;background:var(--white);display:flex}
.field{flex:1;border-right:1px solid #ccc;font-size:7.5px;display:flex;align-items:center;justify-content:space-between;padding:0 8px;color:#222}
.field::after{content:"";border:3px solid transparent;border-top-color:#222;margin-top:3px}
.search-btn{position:absolute;left:590px;top:47px;width:87px;height:29px;background:var(--gold);color:var(--white);font-size:9px;font-weight:700;display:flex;align-items:center;justify-content:center;clip-path:polygon(6% 0,100% 0,100% 100%,0 100%)}
.call{position:absolute;left:0;width:122px;text-align:center;color:var(--white)}
.section-title{position:absolute;left:0;width:688px;text-align:center;font-family:'Cinzel',serif;font-size:15px;color:#111}
.photo{position:absolute}
.about-title{position:absolute;left:383px;top:556px;font-family:'Cinzel',serif;font-size:17px}
.about-copy{position:absolute;left:383px;width:250px;font-size:7.5px;line-height:17.6px;color:#333}
.carousel-arrow{position:absolute;width:24px;height:24px;border-radius:50%;display:flex;align-items:center;justify-content:center;box-shadow:0 1px 4px rgba(0,0,0,.3)}
.step-card{position:absolute;top:1252px;width:172px;height:186px;border:1px solid var(--line);border-radius:2px;text-align:center;background:var(--white)}
.step-card svg{margin-top:18px}
.step-card h3{font-family:'Cinzel',serif;font-size:9.5px;margin-top:6px;letter-spacing:.3px}
.step-card p{font-size:7.5px;line-height:17.6px;color:#444;margin-top:6px;padding:0 20px}
.testimonial{position:absolute;left:133px;top:1568px;width:422px;height:216px;background:var(--white);box-shadow:0 2px 10px rgba(0,0,0,.08);text-align:center;font-family:'Open Sans',sans-serif}
.testimonial__head{font-weight:700;font-size:10px;margin-top:36px}
.testimonial__body{font-size:7.5px;line-height:17.6px;color:#444;margin:10px 26px 0}
.testimonial__name{color:var(--gold);font-size:9.5px;margin-top:14px}
.testimonial__role{font-size:7.5px;color:#333;margin-top:6px}
.avatar{position:absolute;border-radius:50%;border:2px solid var(--white)}
.site-footer{position:absolute;left:0;top:1863px;width:688px;height:307px;background:radial-gradient(ellipse at 50% 30%,#101613 0%,#000 60%)}
.footer-name{position:absolute;left:0;width:688px;top:122px;text-align:center;font-family:'Cinzel',serif;color:var(--gold);font-size:20px}
.footer-nav{position:absolute;left:0;width:688px;top:162px;display:flex;justify-content:center;gap:18px;font-family:'Open Sans',sans-serif;color:var(--white);font-size:8.5px}
.contact-item{position:absolute;top:194px;display:flex;align-items:center;gap:10px;color:var(--white);font-size:8.5px;font-family:'Open Sans',sans-serif;white-space:nowrap}
.contact-item__icon{width:28px;height:26px;background:var(--gold);display:flex;align-items:center;justify-content:center}
.copyright{position:absolute;left:0;width:688px;top:252px;text-align:center;color:var(--white);font-size:8.5px;font-family:'Open Sans',sans-serif}
.copyright span{color:var(--gold)}
</style>
</head>
<body>

<section class="screen screen--landing">
  <div class="landing-bg" role="img" aria-label="Dark abstract background with a faint hexagonal mesh"></div>
  <header class="site-header">
    <div class="brand"><span class="brand__mark"></span>Velmor Spire Nine</div>
    <nav class="nav"><span>HOME</span><span>LOCATION</span><span>EXPERIENCE</span><span>ABOUT US</span></nav>
    <div class="pill" style="left:550px;top:14px;width:81px;height:27px">CONTACT US</div>
  </header>
  <div class="landing-rule"></div>
  <h1 class="landing-title">VELMOR SPIRES</h1>
  <p class="landing-copy">Lorem ipsum dolor sit amet, consectetur adipiscing elit, sed do eiusmod<br>tempor incididunt ut labore et dolore magna aliqua.</p>
  <div class="pill" style="left:202px;top:254px;width:138px;height:28px">VELMOR SPIRE RESIDENCE</div>
  <div class="pill pill--outline" style="left:348px;top:254px;width:139px;height:28px">VELMOR SPIRE OFFICE</div>
</section>

<section class="screen screen--home">
  <header class="site-header">
    <div class="brand"><span class="brand__mark"></span>Velmor Spire Nine</div>
    <nav class="nav"><span>HOME</span><span>LOCATION</span><span>EXPERIENCE</span><span>ABOUT US</span></nav>
    <div class="pill" style="left:550px;top:14px;width:81px;height:27px">CONTACT US</div>
  </header>

  <div class="hero" role="img" aria-label="Photo of a modern white residential building against a blue sky"></div>
  <h1 class="hero-title">WELCOME TO<br>VELMOR SPIRE<br>RESIDENCE</h1>
  <p class="hero-copy">Lorem ipsum dolor sit amet, consectetur elit,<br>eiusmod tempor .</p>
  <div class="pill" style="left:57px;top:286px;width:80px;height:26px">CONTACT US</div>

  <div class="finder">
    <svg class="abs" style="left:0;top:-30px" width="688" height="124" viewBox="0 0 688 124">
      <rect x="0" y="30" width="688" height="94" fill="#000"/>
      <polygon points="0,30 0,124 134,124 112,30" fill="#d4982b"/>
      <polygon points="20,30 62,0 112,30" fill="#d4982b"/>
      <circle cx="61" cy="35" r="18" fill="#000"/>
      <path d="M55 29c0 8 5 13 12 13l2-3-3-2-2 1c-2-1-4-3-5-5l1-2-2-3z" fill="#fff"/>
      <path d="M63 29a5 5 0 0 1 4 4M64 26a8 8 0 0 1 6 6" stroke="#fff" stroke-width="1.2" fill="none"/>
    </svg>
    <div class="call serif" style="top:33px;font-size:11px">CALL NOW :</div>
    <div class="call" style="top:54px;font-size:11px">+1 555 0142 7788</div>
    <div class="finder__label">SKYHAVEN REALTY</div>
    <div class="finder__fields">
      <div class="field">Single Family</div><div class="field">City or Zip</div><div class="field">Beds</div>
      <div class="field">Baths</div><div class="field">Min</div><div class="field" style="border-right:0">Max</div>
    </div>
    <div class="search-btn">SEARCH</div>
  </div>

  <div class="photo" style="left:57px;top:551px;width:254px;height:186px;background:linear-gradient(120deg,#6b4a2c,#b08a5e 50%,#3e2a1a)" role="img" aria-label="Photo of a warm-toned luxury bedroom with palm views"></div>
  <div class="photo" style="left:162px;top:627px;width:168px;height:171px;background:linear-gradient(160deg,#f2ede6,#cfc4b4 70%,#b5a58e)" role="img" aria-label="Photo of a guest relaxing on a sofa"></div>
  <h2 class="about-title">ABOUT US</h2>
  <p class="about-copy" style="top:588px">Lorem ipsum dolor sit amet, consectetur adipiscing elit, sed do eiusmod tempor incididunt ut labore et dolore magna aliqua. Ut enim ad minim veniam, quis nostrud exercitation ullamco laboris nisi ut aliquip ex ea commodo consequat.</p>
  <p class="about-copy" style="top:676px">Duis aute irure dolor in reprehenderit in voluptate velit esse cillum dolore eu fugiat nulla pariatur. Excepteur sint occaecat cupidatat non proident, sunt in culpa qui officia deserunt mollit anim id est laborum.</p>
  <div class="pill" style="left:383px;top:763px;width:81px;height:27px">CONTACT US</div>

  <h2 class="section-title" style="top:864px">LATEST MARKET PLACE DEALS</h2>
  <div class="photo" style="left:0;top:906px;width:106px;height:246px;background:linear-gradient(160deg,#2b2b28,#4a3d2a)" role="img" aria-label="Photo of a dim hotel room"></div>
  <div class="photo" style="left:114px;top:906px;width:459px;height:246px;background:linear-gradient(180deg,#9a9896 0%,#d7d6d2 45%,#6a5a4b 100%)" role="img" aria-label="Photo of a bright bedroom with a white bed and window seating"></div>
  <div class="photo" style="left:581px;top:906px;width:107px;height:246px;background:linear-gradient(160deg,#3b2a1d,#8a6a4a)" role="img" aria-label="Photo of a wood-panelled hotel room"></div>
  <div class="carousel-arrow" style="left:97px;top:1017px;background:#fff"><svg width="8" height="8" viewBox="0 0 8 8"><path d="M5 1 2 4l3 3" stroke="#333" fill="none"/></svg></div>
  <div class="carousel-arrow" style="left:565px;top:1017px;background:var(--gold)"><svg width="8" height="8" viewBox="0 0 8 8"><path d="M3 1l3 3-3 3" stroke="#fff" fill="none"/></svg></div>

  <h2 class="section-title" style="top:1204px;font-size:17px">HOW ITS WORKS</h2>
  <div class="step-card" style="left:57px">
    <svg width="56" height="56" viewBox="0 0 56 56" fill="none" stroke="#1d2a44" stroke-width="1.5"><path d="M8 26 28 8l20 18" stroke="#d4982b"/><path d="M13 22v26h26"/><rect x="19" y="28" width="10" height="10"/><circle cx="39" cy="40" r="7"/><path d="M44 45l6 6"/></svg>
    <h3>LOREM IPSUM DOLOR SIT</h3>
    <p>Sed ut perspiciatis unde omnis iste natus error sit voluptatem accusantium doloremque laudantium, totam rem</p>
  </div>
  <div class="step-card" style="left:257px">
    <svg width="56" height="56" viewBox="0 0 56 56" fill="none" stroke="#1d2a44" stroke-width="1.5"><circle cx="31" cy="14" r="9" fill="#d4982b" stroke="#1d2a44"/><path d="M27 14l3 3 5-6"/><rect x="8" y="34" width="7" height="14" fill="#4a6fa5"/><path d="M15 36h10l10-4c4-1 6 2 3 4l-10 6H15"/></svg>
    <h3>LOREM IPSUM DOLOR SIT</h3>
    <p>Sed ut perspiciatis unde omnis iste natus error sit voluptatem accusantium doloremque laudantium, totam rem</p>
  </div>
  <div class="step-card" style="left:457px">
    <svg width="56" height="56" viewBox="0 0 56 56" fill="none" stroke="#1d2a44" stroke-width="1.5"><rect x="16" y="8" width="24" height="14" fill="#d4982b"/><circle cx="28" cy="15" r="4"/><path d="M8 20c0 12 8 18 14 26M48 20c0 12-8 18-14 26M14 26l8 10M42 26l-8 10"/></svg>
    <h3>LOREM IPSUM DOLOR SIT</h3>
    <p>Sed ut perspiciatis unde omnis iste natus error sit voluptatem accusantium doloremque laudantium, totam rem</p>
  </div>

  <div class="abs" style="left:0;width:688px;top:1494px;text-align:center;color:var(--gold);font-family:'Open Sans',sans-serif;font-size:8.5px;font-weight:600">Testimonials</div>
  <h2 class="section-title" style="top:1516px;font-size:17px">OUR CUSTOMERS, OUR SUCCESS</h2>
  <div class="testimonial">
    <div class="testimonial__head">"A perfect place to book pet friendly vacations!!"</div>
    <p class="testimonial__body">Lorem ipsum dolor sit amet, consectetur adipiscing elit, sed do eiusmod tempor incididunt ut labore et dolore magna aliqua. Ut enim ad minim veniam, quis nostrud exercitation ullamco laboris nisi ut aliquip ex ea commodo consequat.</p>
    <div class="testimonial__name">Marla Quenby</div>
    <div class="testimonial__role">An avid traveler and pet lover</div>
    <svg width="30" height="6" viewBox="0 0 30 6" style="margin-top:6px"><circle cx="5" cy="3" r="2" fill="#f3dcae"/><circle cx="15" cy="3" r="2" fill="#d4982b"/><circle cx="25" cy="3" r="2" fill="#f3dcae"/></svg>
  </div>
  <svg class="abs" style="left:323px;top:1554px" width="42" height="32" viewBox="0 0 42 32"><path d="M2 30V18C2 8 8 3 16 2v6c-5 1-7 4-7 8h7v14zM24 30V18c0-10 6-15 14-16v6c-5 1-7 4-7 8h7v14z" fill="#d4982b"/></svg>
  <svg class="abs" style="left:112px;top:1669px" width="40" height="16" viewBox="0 0 40 16"><path d="M39 8H2M9 1 2 8l7 7" stroke="#111" stroke-width="1.4" fill="none"/></svg>
  <svg class="abs" style="left:536px;top:1669px" width="40" height="16" viewBox="0 0 40 16"><path d="M1 8h37M31 1l7 7-7 7" stroke="#111" stroke-width="1.4" fill="none"/></svg>
  <div class="avatar" style="left:272px;top:1762px;width:38px;height:38px;background:linear-gradient(#c9c2ba,#6f6a66)" role="img" aria-label="Customer portrait"></div>
  <div class="avatar" style="left:319px;top:1756px;width:50px;height:50px;background:linear-gradient(#a8876b,#5e4a3c)" role="img" aria-label="Customer portrait"></div>
  <div class="avatar" style="left:378px;top:1762px;width:38px;height:38px;background:linear-gradient(#eee7e1,#b59a84)" role="img" aria-label="Customer portrait"></div>

  <footer class="site-footer">
    <div class="abs" style="left:338px;top:100px;width:12px;height:12px;background:var(--gold)"></div>
    <div class="footer-name">VELMOR SPIRE NINE</div>
    <nav class="footer-nav"><span>HOME</span><span>ABOUT US</span><span>SERVICES</span><span>TESTIMONIALS</span><span>CONTACT US</span></nav>
    <div class="contact-item" style="left:97px">
      <span class="contact-item__icon"><svg width="14" height="10" viewBox="0 0 14 10"><rect width="14" height="10" fill="#fff"/><path d="M0 0l7 5 7-5" stroke="#d4982b" fill="none"/></svg></span>info@velmorspires.com
    </div>
    <div class="contact-item" style="left:299px">
      <span class="contact-item__icon"><svg width="10" height="14" viewBox="0 0 10 14"><path d="M5 14S0 8 0 5a5 5 0 0 1 10 0c0 3-5 9-5 9z" fill="#fff"/><circle cx="5" cy="5" r="2" fill="#d4982b"/></svg></span>Velmor Spires,United State.
    </div>
    <div class="contact-item" style="left:504px">
      <span class="contact-item__icon"><svg width="12" height="12" viewBox="0 0 12 12"><path d="M1 2c0 5 4 9 9 9l1-2-2-2-2 1C5 7 4 6 3 5l1-2-2-2z" fill="#fff"/></svg></span>+1 555 0142 778
    </div>
    <div class="copyright">Copyrights@2024.<span>Velmor Spires</span>.All Rights Reserved</div>
  </footer>
</section>

</body>
</html>
```